business card for a massage therapy practice named 'Cedar and Willow Massage Studio'

I really need a trendy, yet easy on the eyes business card to complement my logo. Ideally with some gold or rose gold foil work.

My uploaded file of the logo I have in horizontal but I have a vertical version as well. Another color that is used in the website is a blush pink here and there. I'd like to see some trendy tropical leaves in the design.

```html
<!DOCTYPE html>
<html lang="en">
<head>
<meta charset="utf-8">
<title>Cedar &amp; Willow Massage Studio – Business Card</title>
<link href="https://fonts.googleapis.com/css2?family=Open+Sans:wght@400;600&display=swap" rel="stylesheet">
<style>
  :root {
    --backdrop: #1b1b1b;
    --card-light: #f3f3f3;
    --card-mint: #86d4bc;
    --mint-accent: #6fcfb2;
    --ink: #1e1e1e;
    --ink-soft: #333333;
  }
  * { margin: 0; padding: 0; box-sizing: border-box; }
  html, body {
    width: 1200px; height: 900px; overflow: hidden;
    background: var(--backdrop);
    font-family: "Open Sans", Arial, sans-serif;
  }
  .canvas { position: relative; width: 1200px; height: 900px; }

  .card { position: absolute; top: 200px; width: 310px; height: 502px; }
  .card--front { left: 253px; background: var(--card-light); border-radius: 52px 0 52px 0; }
  .card--back  { left: 627px; background: var(--card-mint);  border-radius: 0 52px 0 52px; }

  .brand { position: absolute; display: flex; align-items: center; gap: 12px; }
  .brand__mark { width: 14px; height: 14px; border-radius: 50%; flex: none; }
  .brand__name { font-weight: 600; font-size: 21px; line-height: 1.2; }
  .brand__name span { display: block; font-size: 13px; letter-spacing: 2px; }

  .card--front .brand { left: 34px; top: 132px; }
  .card--front .brand__mark { background: var(--mint-accent); }
  .card--front .brand__name { color: var(--ink); }
  .card--back .brand { left: 34px; top: 146px; }
  .card--back .brand__mark { background: var(--ink); }
  .card--back .brand__name { color: var(--ink); }

  .contact { position: absolute; left: 32px; top: 324px; color: var(--ink-soft); font-size: 15px; line-height: 19px; }
  .contact__name { color: var(--mint-accent); font-size: 18px; font-weight: 600; line-height: 22px; }
  .contact__address { margin-top: 13px; }
  .contact__lines { margin-top: 10px; }
  .contact__line { display: flex; align-items: center; gap: 6px; }
  .contact__line svg { width: 13px; height: 11px; flex: none; }

  .services { position: absolute; left: 40px; top: 317px; list-style: none; color: var(--ink); font-size: 13px; }
  .services li { line-height: 24.6px; display: flex; align-items: center; gap: 5px; }
  .services li::before { content: ""; width: 6px; height: 6px; border-radius: 50%; background: var(--ink); }
</style>
</head>
<body>
<main class="canvas">
  <section class="card card--front">
    <div class="brand">
      <span class="brand__mark"></span>
      <p class="brand__name">Cedar &amp; Willow<span>MASSAGE STUDIO</span></p>
    </div>
    <div class="contact">
      <p class="contact__name">MARISOL BENNETT</p>
      <p class="contact__title">Massage Therapist</p>
      <p class="contact__address">2145 J St. suite 210<br>Sacramento, CA 95816</p>
      <div class="contact__lines">
        <p class="contact__line">
          <svg viewBox="0 0 13 11" aria-hidden="true"><path fill="#6fcfb2" d="M1 4c0-2 2.5-3 5.5-3S12 2 12 4l-2.5.6L9 3.4H4l-.5 1.2zM3 6l1.5-2h4L10 6v4H3z"/></svg>
          (916) 555-0148
        </p>
        <p class="contact__line">
          <svg viewBox="0 0 13 11" aria-hidden="true"><rect x="0.5" y="1" width="12" height="9" fill="#6fcfb2"/><path d="M0.5 1l6 5 6-5" fill="none" stroke="#f3f3f3" stroke-width="1"/></svg>
          cedarandwillow@gmail.com
        </p>
      </div>
    </div>
  </section>

  <section class="card card--back">
    <div class="brand">
      <span class="brand__mark"></span>
      <p class="brand__name">Cedar &amp; Willow<span>MASSAGE STUDIO</span></p>
    </div>
    <ul class="services">
      <li>CLINICAL BODYWORK</li>
      <li>THERAPEUTIC MASSAGE</li>
      <li>INTEGRATED HOT STONE MASSAGE</li>
      <li>LYMPHATIC DRAINAGE MASSAGE</li>
      <li>SACRAMENTO SINUS FACIAL</li>
      <li>AUSTRALIAN FOOT TREATMENT</li>
    </ul>
  </section>
</main>
</body>
</html>
```